Steady Hands, professional newsletter for GAPM

** updated based on results so far** We need a 2 page newsletter designed on both sides of an 8.6 x 11 sheet back and front. Page one needs our logo below, name steady hands in large letters tagline of official newsletter of the guild of acute practice medicine volume and issue number locations It needs to include five locations for 250-400 word articles each with a spot for a picture. Page 2 needs to include contact information including address, phone number, email, twitter and facebook info below. The design need to complement out log in color, be professional with clean lines and easy to follow. We are a non profit organization dedicated to providers of urgent care medicine.

Target Market(s)

Physicians, Nurse Practitioners, Physician Assistants

Requirements
Must have
• 2 pages, back and front 8.5x 11
• 5 article area 250-400 words, one image for each
• our logo
• Name: Steady Hands - page one large visible print
• Contact inf:
• Guild of Acute Practice Medicine
• 912 Larkmoor Ave. Suite 418E
• Naperville, IL 60563
• 1 855-314-7093
• Info@gaopm.org
• @GuildAPM
Nice to have
• ease of entering info
• professional clean lines

```html
<!DOCTYPE html>
<html lang="en">
<head>
<meta charset="utf-8">
<title>Steady Hands – Newsletter Cover</title>
<link href="https://fonts.googleapis.com/css2?family=Open+Sans:wght@400;600;700;800&display=swap" rel="stylesheet">
<style>
  :root {
    --backdrop: #ece3e3;
    --paper: #ffffff;
    --amber: #f0a632;
    --brick: #b83b27;
    --ink: #3c3c3c;
    --body-ink: #555555;
    --photo-blue: #3b78b9;
  }
  * { box-sizing: border-box; margin: 0; padding: 0; }
  html, body { width: 1200px; height: 1200px; overflow: hidden; }
  body {
    background: var(--backdrop);
    font-family: "Open Sans", Arial, sans-serif;
    position: relative;
  }
  .cover {
    position: absolute;
    left: 208px; top: 40px;
    width: 784px; height: 1120px;
    background: var(--paper);
    box-shadow: 0 2px 10px rgba(0,0,0,0.12);
    overflow: hidden;
  }
  .issue-bar {
    position: absolute; left: 0; top: 0; width: 100%; height: 38px;
    background: var(--amber);
    color: #fff; font-weight: 700; font-size: 14px; letter-spacing: 1px;
    display: flex; justify-content: space-between; align-items: center;
    padding: 0 60px 0 27px;
  }
  .masthead {
    position: absolute; left: 0; top: 50px; width: 100%;
    text-align: center;
    font-weight: 800; font-size: 88px; line-height: 1.1;
    color: var(--ink); letter-spacing: -1px;
  }
  .org-mark {
    position: absolute; top: 170px; left: 0; width: 100%;
    display: flex; justify-content: center; align-items: center; gap: 10px;
  }
  .org-mark .dot {
    width: 22px; height: 22px; border-radius: 50%; background: var(--brick);
  }
  .org-mark .name {
    font-size: 17px; line-height: 22px; font-weight: 600; color: var(--ink);
  }
  .tagline-band { position: absolute; left: 0; top: 239px; width: 784px; height: 30px; }
  .tagline-band span {
    position: absolute; left: 90px; top: 0; line-height: 30px;
    color: #fff; font-weight: 700; font-size: 14px;
  }
  .article { position: absolute; left: 40px; width: 697px; overflow: hidden; }
  .article h2 {
    font-size: 16px; font-weight: 700; color: var(--ink);
    margin-bottom: 6px;
  }
  .article p {
    font-size: 12.6px; line-height: 16.8px; color: var(--body-ink);
    text-align: justify; margin-bottom: 16px;
  }
  .lead-story { top: 292px; height: 535px; }
  .second-story { top: 842px; height: 240px; }
  .photo-slot {
    background: var(--photo-blue); color: #fff;
    display: flex; flex-direction: column; align-items: center; justify-content: center;
  }
  .photo-slot strong { font-weight: 700; }
  .photo-slot small { font-size: 16px; font-weight: 400; opacity: 0.9; }
  .lead-story .photo-slot {
    float: left; width: 354px; height: 298px; margin: 6px 19px 10px 0;
  }
  .lead-story .photo-slot strong { font-size: 30px; }
  .second-story .photo-slot {
    float: right; width: 267px; height: 193px; margin: 20px 0 10px 40px;
  }
  .second-story .photo-slot strong { font-size: 25px; }
  .second-story .photo-slot small { font-size: 14px; }
  .footer-band { position: absolute; left: 0; bottom: 2px; width: 784px; height: 25px; }
</style>
</head>
<body>
  <main class="cover">
    <header class="issue-bar">
      <span>VOLUME - 01 | ISSUE - 001</span>
      <span>WWW. GAOPM.ORG</span>
    </header>

    <h1 class="masthead">STEADY HANDS</h1>

    <div class="org-mark">
      <span class="dot"></span>
      <span class="name">Guild of Acute Practice Medicine</span>
    </div>

    <div class="tagline-band">
      <svg width="784" height="30" viewBox="0 0 784 30">
        <rect width="784" height="30" fill="var(--amber)"/>
        <polygon points="690,30 720,0 784,0 784,30" fill="var(--brick)"/>
      </svg>
      <span>OFFICIAL NEWSLETTER OF THE GUILD OF ACUTE PRACTICE MEDICINE</span>
    </div>

    <article class="article lead-story">
      <h2>THIS IS DUMMY TITLE 01 GENERATED</h2>
      <p>Lorem ipsum dolor sit amet, consectetuer adipiscing elit. Aenean commodo ligula eget dolor. Aenean massa. Cum sociis natoque penatibus et magnis dis parturient montes, nascetur ridiculus mus.</p>
      <p>Donec quam felis, ultricies nec, pellentesque eu, pretium quis, sem. Nulla consequat massa quis enim. Donec pede justo, fringilla vel, aliquet nec, vulputate eget, arcu. In enim justo, rhoncus ut, imperdiet a, venenatis vitae, justo. Nullam dictum felis eu pede mollis pretium. Integer tincidunt. Cras dapibus. Vivamus elementum semper nisi.</p>
      <div class="photo-slot" role="img" aria-label="Photo for the first article">
        <strong>Placeholder Image</strong><small>Lorem Ipsum</small>
      </div>
      <p>Aenean vulputate eleifend tellus. Aenean leo ligula, porttitor eu, consequat vitae, eleifend ac, enim. Aliquam lorem ante, dapibus in, viverra quis, feugiat a, tellus. Phasellus viverra nulla ut metus varius laoreet. Quisque rutrum. Aenean imperdiet. Etiam ultricies nisi vel augue. Curabitur ullamcorper ultricies nisi. Nam eget dui. Etiam rhoncus. Maecenas tempus, tellus eget condimentum rhoncus, sem quam semper libero, sit amet adipiscing sem neque sed ipsum. Nam quam nunc, blandit vel, luctus pulvinar, hendrerit id, lorem. Maecenas nec odio et ante tincidunt tempus.</p>
      <p>Donec vitae sapien ut libero venenatis faucibus. Nullam quis ante. Etiam sit amet orci eget eros faucibus tincidunt. Duis leo. Sed fringilla mauris sit amet nibh. Donec sodales sagittis magna. Sed consequat, leo eget bibendum sodales, augue velit cursus nunc, quis gravida magna mi a libero. Fusce vulputate eleifend sapien. Vestibulum purus quam, scelerisque ut, mollis sed, nonummy id, metus. Nullam accumsan lorem in dui. Cras ultricies mi eu turpis hendrerit fringilla. Vestibulum ante ipsum primis in faucibus orci luctus et ultrices posuere cubilia Curae; In ac dui quis mi.</p>
    </article>

    <article class="article second-story">
      <div class="photo-slot" role="img" aria-label="Photo for the second article">
        <strong>Placeholder Image</strong><small>Lorem Ipsum</small>
      </div>
      <h2>THIS IS DUMMY TITLE 02 GENERATED</h2>
      <p>Lorem ipsum dolor sit amet, consectetuer adipiscing elit. Aenean commodo ligula eget dolor. Aenean massa. Cum sociis natoque penatibus et magnis dis parturient montes, nascetur ridiculus mus. Donec quam felis, ultricies nec, pellentesque eu, pretium quis, sem. Nulla consequat massa quis enim. Donec pede justo, fringilla vel, aliquet nec, vulputate eget, arcu. In enim justo, rhoncus ut, imperdiet a, venenatis vitae, justo. Nullam dictum felis eu pede mollis pretium. Integer tincidunt. Cras dapibus. Vivamus elementum semper nisi. Aenean vulputate eleifend tellus. Aenean leo ligula, porttitor eu, consequat vitae, eleifend ac, enim. Aliquam lorem ante, dapibus in, viverra quis, feugiat a, tellus.</p>
    </article>

    <div class="footer-band">
      <svg width="784" height="25" viewBox="0 0 784 25">
        <rect width="784" height="25" fill="var(--amber)"/>
        <polygon points="466,25 490,0 784,0 784,25" fill="var(--brick)"/>
      </svg>
    </div>
  </main>
</body>
</html>
```